New Business Card Design Project

I need a design for business cards, i am an electrical business called "Corvane Electrical and Communications" i need the cards to be double sided with the company logo on the back (attached) the front needs to say my company name, web site, email address, telephone number, and ABN number and electrical license number. I am open to different arrangements of the information but would like the background to be incorporating something electrical or something that looks smart. open to all additional ideas also.

The company colours are orange and grey see logo attached.

Business Name: Corvane Electrical and Communications
Website: corvaneelectricalandcomms.example.com.au
Email: brent@corvaneelectricalandcomms.example.com.au
Telephone(mobile): 0481209736
ABN: 71208349162
Lic No: 418273D

Target Market(s)

Business entities, Project Managers, Accounts, Clients

Industry/Entity Type

Electrician

Contact Information for Business Card

I need a design for business cards, i am an electrical business called "Corvane Electrical and Communications" i need the cards to be double sided with the company logo on the back (attached) the front needs to say my company name

Font styles to use
Serif
Sans Serif

Colors
f37122
5c5c5c

Requirements
Must have
• Must have the Logo on the back open to different ways of it being on the back but had in mind to keep it central but again open to other options
Nice to have
• A real modern cool background that is eye catching yet contemporary
Should not have
• No backgrounds of a light bulb or plug or anything like that

```html
<!DOCTYPE html>
<html lang="en">
<head>
<meta charset="utf-8">
<title>Corvane Electrical and Communications – Business Cards</title>
<link href="https://fonts.googleapis.com/css2?family=Open+Sans:wght@400;600&display=swap" rel="stylesheet">
<style>
  :root {
    --orange: #f7a21b;
    --grey-dark: #565656;
    --grey-text: #5c5c5c;
    --white: #ffffff;
    --stage: #2b2b2b;
    --rule: #7a7a7a;
  }
  * { margin: 0; padding: 0; box-sizing: border-box; }
  html, body { width: 1200px; height: 900px; overflow: hidden; }
  body {
    background: var(--stage);
    font-family: "Open Sans", Arial, sans-serif;
    position: relative;
  }
  .card {
    position: absolute;
    left: 280px;
    width: 640px;
    height: 366px;
    border-radius: 26px;
    overflow: hidden;
  }
  .card-back { top: 56px; background: var(--grey-dark); }
  .card-front { top: 478px; background: var(--white); }
  .card-bands { position: absolute; left: 0; bottom: 0; width: 640px; height: 80px; }

  .brand { position: absolute; display: flex; align-items: center; gap: 16px; }
  .brand-dot { width: 22px; height: 22px; border-radius: 50%; background: var(--orange); flex: none; }
  .brand-text { font-weight: 600; line-height: 1.05; }
  .brand-name { font-size: 58px; letter-spacing: 3px; text-transform: uppercase; display: block; }
  .brand-sub { font-size: 15.5px; letter-spacing: 1.6px; text-transform: uppercase; display: block; margin-top: 6px; }

  .card-back .brand { left: 78px; top: 112px; }
  .card-back .brand-text { color: var(--white); }
  .back-web {
    position: absolute; right: 46px; top: 262px;
    font-size: 14.5px; color: var(--white);
  }

  .card-front .brand { left: 52px; top: 226px; }
  .card-front .brand-name { font-size: 44px; }
  .card-front .brand-sub { font-size: 12px; letter-spacing: 1.2px; }
  .card-front .brand-text { color: var(--grey-text); }

  .person { position: absolute; right: 40px; top: 30px; text-align: right; }
  .person-name { font-size: 22px; color: var(--orange); letter-spacing: 0.5px; text-transform: uppercase; }
  .person-role { font-size: 11px; font-weight: 600; color: var(--grey-text); letter-spacing: 0.5px; margin-top: 2px; }
  .name-rule { position: absolute; left: 250px; top: 66px; width: 260px; height: 1.5px; background: var(--rule); }
  .mid-rule { position: absolute; left: 44px; top: 178px; width: 180px; height: 1.5px; background: var(--rule); }

  .contact {
    position: absolute; right: 36px; top: 130px;
    list-style: none; text-align: right;
    font-size: 12.5px; color: var(--grey-text); line-height: 1.55;
  }
  .contact li { display: flex; justify-content: flex-end; align-items: center; gap: 8px; }
  .contact .abn { margin-bottom: 8px; }
  .contact .label { color: var(--orange); font-weight: 600; }
  .contact svg { width: 12px; height: 12px; flex: none; }
  .contact .no-icon { padding-right: 20px; }
  .licence {
    position: absolute; right: 34px; bottom: 50px;
    font-size: 12.5px; color: var(--grey-text);
  }
  .licence .label { color: var(--grey-text); }
</style>
</head>
<body>

  <section class="card card-back" aria-label="Card back">
    <div class="brand">
      <span class="brand-dot"></span>
      <span class="brand-text">
        <span class="brand-name">Corvane</span>
        <span class="brand-sub">Electrical &amp; Communications</span>
      </span>
    </div>
    <p class="back-web">www.corvaneelectricalandcomms.example.com.au</p>
    <svg class="card-bands" viewBox="0 0 640 80" aria-hidden="true">
      <rect x="0" y="60" width="640" height="20" fill="var(--orange)"/>
      <rect x="0" y="36" width="260" height="24" fill="var(--orange)"/>
      <rect x="260" y="0" width="200" height="60" fill="var(--white)"/>
      <rect x="460" y="0" width="180" height="60" fill="var(--orange)"/>
    </svg>
  </section>

  <section class="card card-front" aria-label="Card front">
    <div class="person">
      <p class="person-name">Marlo Grant</p>
      <p class="person-role">DIRECTOR</p>
    </div>
    <div class="name-rule"></div>
    <div class="mid-rule"></div>

    <ul class="contact">
      <li class="abn no-icon"><span><span class="label">ABN:</span> 71208349162</span></li>
      <li><span>0481-209-736</span>
        <svg viewBox="0 0 12 12"><path d="M2.5 1h2l1 3-1.5 1a6 6 0 0 0 3 3l1-1.5 3 1v2a1 1 0 0 1-1 1A9.5 9.5 0 0 1 1.5 2a1 1 0 0 1 1-1z" fill="var(--orange)"/></svg></li>
      <li><span>brent@corvaneelectricalandcomms.example.com.au</span>
        <svg viewBox="0 0 12 12"><rect x="1" y="2.5" width="10" height="7" rx="1" fill="none" stroke="var(--orange)" stroke-width="1.3"/><path d="M1.5 3l4.5 3.5L10.5 3" fill="none" stroke="var(--orange)" stroke-width="1.3"/></svg></li>
      <li><span>www.corvaneelectricalandcomms.example.com.au</span>
        <svg viewBox="0 0 12 12"><circle cx="6" cy="6" r="4.8" fill="none" stroke="var(--orange)" stroke-width="1.2"/><path d="M1.2 6h9.6M6 1.2c-2.4 2.6-2.4 7 0 9.6M6 1.2c2.4 2.6 2.4 7 0 9.6" fill="none" stroke="var(--orange)" stroke-width="1"/></svg></li>
    </ul>

    <div class="brand">
      <span class="brand-dot"></span>
      <span class="brand-text">
        <span class="brand-name">Corvane</span>
        <span class="brand-sub">Electrical &amp; Communications</span>
      </span>
    </div>

    <svg class="card-bands" viewBox="0 0 640 80" aria-hidden="true">
      <rect x="0" y="60" width="640" height="20" fill="var(--orange)"/>
      <rect x="0" y="40" width="260" height="20" fill="var(--orange)"/>
      <rect x="260" y="20" width="200" height="40" fill="var(--grey-dark)"/>
      <rect x="460" y="0" width="180" height="60" fill="var(--orange)"/>
    </svg>
    <p class="licence"><span class="label">Lic No:</span> 418273D</p>
  </section>

</body>
</html>
```